Corvane Holdings , new business card design

investment firm with corporate clients . need double sided business card , vertical and horizontal options ,logo must be clear. prefer pantone colors only and sharp design. website also www.corvane.ae

Khalid Bin Tarrafi
Managing Director
Tel. +971 4 387 2940
Mobile +971 50 518 2403
khalid@corvane.ae
Q-Span Plaza, officw 18-B07, Warqa Gardens, Dubai

Contact Information for Business Card

Khalid Bin Tarrafi
Managing Director

Font styles to use
Serif

Colors

Designer to choose colors to be used in the design.

```html
<!DOCTYPE html>
<html lang="en">
<head>
<meta charset="utf-8">
<title>Corvane Holdings – Business Card</title>
<link href="https://fonts.googleapis.com/css2?family=Open+Sans:wght@300;400;700&display=swap" rel="stylesheet">
<style>
  :root {
    --backdrop: #e6e7ea;
    --card: #ffffff;
    --navy: #0d2a6b;
    --steel: #5a7aa6;
    --strip: #5b5670;
    --ink: #2b2b2b;
    --rule: #6d6d6d;
  }
  * { margin: 0; padding: 0; box-sizing: border-box; }
  html, body { width: 1200px; height: 900px; overflow: hidden; }
  body {
    background: var(--backdrop);
    font-family: "Open Sans", Arial, sans-serif;
    color: var(--ink);
    position: relative;
  }
  .card {
    position: absolute;
    width: 560px;
    height: 320px;
    background: var(--card);
    border-radius: 16px;
    overflow: hidden;
    box-shadow: 0 10px 30px rgba(0,0,0,.18);
  }
  .card--contact { left: 320px; top: 90px; }
  .card--brand { left: 320px; top: 490px; }

  .bottom-strip {
    position: absolute;
    left: 0; right: 0; bottom: 0;
    height: 14px;
    background: var(--strip);
  }
  .navy-tab { position: absolute; bottom: 0; }
  .card--contact .navy-tab { right: 0; width: 200px; height: 58px; }
  .card--brand .navy-tab { left: 0; width: 250px; height: 46px; }

  .wordmark {
    display: flex;
    align-items: center;
    gap: 10px;
    font-family: "Open Sans", Arial, sans-serif;
    font-weight: 300;
    color: var(--navy);
    letter-spacing: 0.22em;
    text-transform: uppercase;
    white-space: nowrap;
  }
  .wordmark__square {
    width: 14px; height: 14px;
    background: var(--steel);
    flex: none;
  }
  .card--contact .wordmark { position: absolute; left: 40px; top: 78px; font-size: 22px; }
  .card--brand .wordmark {
    position: absolute; left: 0; right: 0; top: 128px;
    justify-content: center; font-size: 30px;
  }

  .identity {
    position: absolute;
    right: 40px;
    top: 138px;
    text-align: right;
  }
  .identity__name {
    font-weight: 700;
    font-size: 19px;
    color: var(--navy);
  }
  .identity__title {
    font-weight: 300;
    font-size: 14px;
    margin-top: 4px;
  }
  .divider {
    position: absolute;
    left: 0;
    top: 187px;
    width: 350px;
    height: 1px;
    background: var(--rule);
  }
  .address {
    position: absolute;
    right: 40px;
    top: 206px;
    text-align: right;
    font-weight: 300;
    font-size: 14px;
    line-height: 1.35;
  }
  .contacts {
    position: absolute;
    left: 40px;
    top: 206px;
    list-style: none;
    font-size: 15px;
    font-weight: 300;
    line-height: 1.4;
  }
  .contacts li { display: flex; align-items: center; gap: 8px; }
  .contacts svg { width: 12px; height: 12px; fill: var(--navy); flex: none; }

  .website {
    position: absolute;
    left: 30px;
    bottom: 16px;
    color: #fff;
    font-size: 15px;
    letter-spacing: 0.3em;
    font-weight: 400;
  }
</style>
</head>
<body>

  <section class="card card--contact">
    <div class="wordmark"><span class="wordmark__square"></span>Corvane Holdings</div>

    <div class="identity">
      <div class="identity__name">Khalid Bin Tarrafi</div>
      <div class="identity__title">Managing Director</div>
    </div>
    <div class="divider"></div>

    <div class="address">Q-Span Plaza, officw 18-B07,<br>Warqa Gardens, Dubai</div>

    <ul class="contacts">
      <li>
        <svg viewBox="0 0 24 24" aria-hidden="true"><path d="M6.6 10.8a15.5 15.5 0 0 0 6.6 6.6l2.2-2.2c.3-.3.7-.4 1-.2 1.1.4 2.3.6 3.6.6.6 0 1 .4 1 1V20c0 .6-.4 1-1 1A17 17 0 0 1 3 4c0-.6.4-1 1-1h3.5c.6 0 1 .4 1 1 0 1.3.2 2.5.6 3.6.1.3 0 .7-.2 1z"/></svg>
        +971 4 387 2940
      </li>
      <li>
        <svg viewBox="0 0 24 24" aria-hidden="true"><path d="M7 1h10a2 2 0 0 1 2 2v18a2 2 0 0 1-2 2H7a2 2 0 0 1-2-2V3a2 2 0 0 1 2-2zm0 3v14h10V4zm5 15.5a1 1 0 1 0 0 2 1 1 0 0 0 0-2z"/></svg>
        +971 50 518 2403
      </li>
      <li>
        <svg viewBox="0 0 24 24" aria-hidden="true"><path d="M2 5h20v14H2zm2 2v.4l8 5.2 8-5.2V7zm0 2.8V17h16V9.8l-8 5.2z"/></svg>
        khalid@corvane.ae
      </li>
    </ul>

    <div class="bottom-strip"></div>
    <svg class="navy-tab" viewBox="0 0 200 58" preserveAspectRatio="none" aria-hidden="true">
      <polygon points="8,0 200,0 200,58 0,58" fill="var(--navy)"/>
    </svg>
  </section>

  <section class="card card--brand">
    <div class="wordmark"><span class="wordmark__square"></span>Corvane Holdings</div>

    <div class="bottom-strip"></div>
    <svg class="navy-tab" viewBox="0 0 250 46" preserveAspectRatio="none" aria-hidden="true">
      <polygon points="0,0 226,0 250,46 0,46" fill="var(--navy)"/>
    </svg>
    <div class="website">www.corvane.ae</div>
  </section>

</body>
</html>
```